Forensic Document Examiner, looking for contemporary update to my stationery design.

Looking for professional, classy logo design for stationery and business cards. My current stationery and business card is attached.I believe a logo image makes a header section interesting, so an intriguing design of a pen, feathered pen, microscope, magnifying glass, etc., would be appropriate. I have been in the business for over 30 years. I leave ideas to the imagination of the designer.My work involves mainly, the comparison of signatures and handwriting. I also resolve alterations, obliterations, and work as shown on my website: www.documentexaminer.infoThe image produced will be printed on quality white stationery and envelopes. The stationery will be photocopied by my clients, so the images should be reproducible. The business cards may be designed in other than white.

Target Market(s)

Attorneys

Font styles to use
Sans Serif

Colors

Designer to choose colors to be used in the design.

Requirements
Must have
• Image suitable for white stationery and photocopying.
• Classy logo and image; no casual fonts.
Nice to have
• Intriguing, contemporary design incorporating a relevant logo to my work.

```html
<!DOCTYPE html>
<html lang="en">
<head>
<meta charset="utf-8">
<title>Elena R. Marsh — Stationery</title>
<link rel="stylesheet" href="https://fonts.googleapis.com/css2?family=Didact+Gothic&family=Open+Sans:wght@400;600&family=Roboto+Slab:wght@400&display=swap">
<style>
  :root {
    --backdrop: #dcdcdc;
    --paper: #f3f3f3;
    --charcoal: #2e2e2e;
    --ink: #555555;
    --white: #ffffff;
    --accent-yellow: #f2d21c;
    --accent-blue: #2f3193;
    --shadow: 0 2px 5px rgba(0,0,0,.18);
  }
  * { box-sizing: border-box; margin: 0; padding: 0; }
  html, body { width: 1200px; height: 877px; overflow: hidden; background: var(--backdrop); }
  body { position: relative; font-family: "Didact Gothic", sans-serif; }

  .sheet, .envelope { position: absolute; background: var(--paper); box-shadow: var(--shadow); overflow: hidden; }

  .letterhead { left: 58px; top: 65px; width: 528px; height: 743px; }
  .letterhead__header { height: 108px; background: var(--charcoal); position: relative; }

  .brand { position: absolute; color: var(--white); }
  .brand__name { font-family: "Roboto Slab", serif; font-size: 22px; letter-spacing: 2px; line-height: 1; white-space: nowrap; }
  .brand__tagline { font-family: "Open Sans", sans-serif; font-weight: 600; font-size: 8.5px; color: var(--accent-yellow); margin-top: 5px; }
  .letterhead .brand { left: 47px; top: 34px; }

  .contact { position: absolute; left: 351px; top: 28px; list-style: none; font-family: "Open Sans", sans-serif; font-size: 7.8px; color: var(--white); line-height: 10.5px; }
  .contact li { display: flex; gap: 6px; align-items: flex-start; margin-bottom: 2px; }
  .contact svg, .env-address svg { flex: none; width: 8px; height: 8px; margin-top: 1px; fill: var(--accent-yellow); }

  .letter { position: absolute; left: 46px; top: 211px; width: 440px; color: var(--ink); }
  .letter__salutation { font-size: 13.5px; margin-bottom: 24px; }
  .letter p { font-size: 7.6px; line-height: 11.4px; margin-bottom: 11px; text-align: justify; }
  .letter__closing { margin-top: 20px; font-size: 7.6px; }
  .signature { display: block; width: 62px; height: 26px; margin-top: 8px; background: linear-gradient(90deg, rgba(40,40,40,.25), rgba(40,40,40,.05)); border-radius: 2px; }

  .accent-bar { position: absolute; left: 0; bottom: 0; width: 100%; height: 6px; display: flex; }
  .accent-bar__blue { flex: 0 0 79%; background: var(--accent-blue); }
  .accent-bar__yellow { flex: 1; background: var(--accent-yellow); margin-left: 2px; }

  .envelope--back { left: 620px; top: 292px; width: 530px; height: 241px; }
  .flap { position: absolute; left: 0; top: 0; width: 530px; height: 75px; }
  .flap__name { position: absolute; left: 0; width: 530px; top: 32px; text-align: center; color: var(--white); font-family: "Roboto Slab", serif; font-size: 10px; letter-spacing: 1.5px; }

  .envelope--front { left: 620px; top: 563px; width: 532px; height: 242px; }
  .envelope__header { height: 108px; background: var(--charcoal); position: relative; }
  .envelope--front .brand { left: 66px; top: 27px; }
  .env-address { position: absolute; left: 33px; top: 78px; display: flex; gap: 6px; font-family: "Open Sans", sans-serif; font-size: 7.8px; color: var(--white); }
</style>
</head>
<body>

<section class="sheet letterhead">
  <header class="letterhead__header">
    <div class="brand">
      <div class="brand__name">ELENA R. MARSH</div>
      <div class="brand__tagline">Forensic Document Examiner</div>
    </div>
    <ul class="contact">
      <li><svg viewBox="0 0 10 10"><path d="M5 0a3.6 3.6 0 0 0-3.6 3.6C1.4 6.3 5 10 5 10s3.6-3.7 3.6-6.4A3.6 3.6 0 0 0 5 0zm0 5a1.4 1.4 0 1 1 0-2.8A1.4 1.4 0 0 1 5 5z"/></svg><span>P.O.Box 4821,<br>Salem, OR 97301</span></li>
      <li><svg viewBox="0 0 10 10"><path d="M2 .5l2 2-1 1.3a6 6 0 0 0 3.2 3.2L7.5 6l2 2-1.3 1.6C4.6 9.8.2 5.4.4 1.8z"/></svg><span>(555) 210-4476</span></li>
      <li><svg viewBox="0 0 10 10"><path d="M0 2h10v6H0zM0 2l5 3.5L10 2v1L5 6.5 0 3z"/></svg><span>emarsh@quillmarkreview.info</span></li>
      <li><svg viewBox="0 0 10 10"><circle cx="5" cy="5" r="4.6"/></svg><span>www.quillmarkreview.info</span></li>
    </ul>
  </header>

  <article class="letter">
    <p class="letter__salutation">Dear Mr. Porter,</p>
    <p>Lorem ipsum dolor sit amet, consectetur adipiscing elit. Donec orci purus, luctus vitae dignissim eu, iaculis sed purus. Vivamus faucibus, ipsum nec aliquet viverra, leo mauris condimentum ligula, sit amet sagittis enim ligula quis arcu. Nam egestas tortor id nisi porttitor mattis. In tortor ante, ultricies in suscipit a, tempus non massa. Vivamus et auctor mi. Fusce vel massa nulla. Phasellus nec eros mauris, et scelerisque orci.</p>
    <p>Donec malesuada orci vitae nulla accumsan porta a id massa. Quisque accumsan iaculis magna sit amet fringilla. Maecenas consequat, magna eget tincidunt semper, odio nibh rutrum mi, id feugiat ante nisi eu risus. Vestibulum nunc orci, rhoncus a placerat in, ultricies in mi. Cras mattis varius eros, vel fringilla nisi suscipit eget. Quisque scelerisque sagittis nulla at porttitor.</p>
    <p>Sed id augue vitae urna euismod commodo aliquet a quam. Pellentesque arcu velit, cursus et malesuada ut, consequat et diam. Nullam erat sem, rhoncus id ullamcorper vitae, rhoncus et arcu. In ultricies ultricies nulla, ut rutrum nisi iaculis at. Donec eu magna a metus ornare faucibus. Fusce aliquet faucibus ultricies. Morbi semper, est id tincidunt gravida, sem arcu adipiscing lacus, ac bibendum nulla leo eu purus. Quisque nec diam sed risus consectetur a ccumsan quis quis nibh. Vestibulum id purus lorem.</p>
    <p>It is a long established fact that a reader will be distracted by the readable content of a page when looking at its layout. The point of using Lorem Ipsum is that it has a more-or-less normal distribution of letters, as opposed to using 'Content here, content here', making it look like readable English. Many desktop publishing packages</p>
    <p class="letter__closing">Sincerely,</p>
    <span class="signature" role="img" aria-label="Handwritten signature"></span>
  </article>

  <div class="accent-bar"><span class="accent-bar__blue"></span><span class="accent-bar__yellow"></span></div>
</section>

<section class="envelope envelope--back">
  <svg class="flap" viewBox="0 0 530 75" aria-hidden="true">
    <path d="M2 0H528L518 55Q514 75 494 75H36Q16 75 12 55Z" fill="#2e2e2e"/>
  </svg>
  <div class="flap__name">ELENA R. MARSH</div>
</section>

<section class="envelope envelope--front">
  <header class="envelope__header">
    <div class="brand">
      <div class="brand__name">ELENA R. MARSH</div>
      <div class="brand__tagline">Forensic Document Examiner</div>
    </div>
    <div class="env-address">
      <svg viewBox="0 0 10 10"><path d="M5 0a3.6 3.6 0 0 0-3.6 3.6C1.4 6.3 5 10 5 10s3.6-3.7 3.6-6.4A3.6 3.6 0 0 0 5 0zm0 5a1.4 1.4 0 1 1 0-2.8A1.4 1.4 0 0 1 5 5z"/></svg>
      <span>P.O.Box 4821, Salem, OR 97301</span>
    </div>
  </header>
  <div class="accent-bar"><span class="accent-bar__blue"></span><span class="accent-bar__yellow"></span></div>
</section>

</body>
</html>
```